Sparrow Haulage needs a business card design.

Design a double-sided business card for new freight business. On the front, would like to see our logo along with the following info:

Martin Obuya
CEO/FOUNDER
555-206-7142
martinobuya@sparrow-haulage.example

On the reverse side, we would like to use the graphic image of our logo only without the Sparrow Haulage name.

```html
<!DOCTYPE html>
<html lang="en">
<head>
<meta charset="UTF-8">
<title>Sparrow Haulage — Business Card</title>
<link href="https://fonts.googleapis.com/css2?family=Montserrat:wght@700;800&family=Open+Sans:wght@400;600&display=swap" rel="stylesheet">
<style>
  :root {
    --navy: #1c1a5c;
    --red: #b31f27;
    --paper: #ffffff;
    --backdrop: #e9e6e1;
  }
  * { box-sizing: border-box; margin: 0; padding: 0; }
  html, body {
    width: 1200px; height: 900px; overflow: hidden;
    background: var(--backdrop);
  }
  .canvas { position: relative; width: 1200px; height: 900px; }
  .card {
    position: absolute; left: 280px; width: 640px; height: 366px;
    background: var(--paper); border-radius: 26px; overflow: hidden;
    box-shadow: 0 10px 28px rgba(0,0,0,.18);
  }
  .card--front { top: 50px; }
  .card--back { top: 484px; }

  .brand {
    position: absolute; left: 40px; top: 38px;
    display: flex; align-items: center; gap: 12px;
  }
  .brand__square { width: 22px; height: 22px; background: var(--red); }
  .brand__name {
    font-family: "Montserrat", sans-serif; font-weight: 800;
    font-size: 26px; letter-spacing: 2px; text-transform: uppercase;
    color: var(--navy); line-height: 1;
  }

  .contact { position: absolute; left: 40px; top: 130px; width: 320px; }
  .contact__name {
    font-family: "Montserrat", sans-serif; font-weight: 700;
    font-size: 22px; color: var(--navy);
  }
  .contact__role {
    font-family: "Open Sans", sans-serif; font-weight: 400;
    font-size: 15px; color: var(--red); margin-top: 2px; letter-spacing: .5px;
  }
  .contact__list { list-style: none; margin-top: 14px; }
  .contact__item {
    display: flex; align-items: center; gap: 8px;
    font-family: "Open Sans", sans-serif; font-size: 14px; color: var(--navy);
    margin-bottom: 6px; white-space: nowrap;
  }
  .contact__icon { width: 14px; height: 14px; flex: none; }

  .front-graphic {
    position: absolute; left: 390px; top: 110px; width: 250px; height: 256px;
  }

  .back-pattern { position: absolute; inset: 0; width: 100%; height: 100%; }
  .back-mark {
    position: absolute; left: 50%; top: 50%;
    width: 40px; height: 40px; margin: -20px 0 0 -20px;
    background: var(--red);
  }
</style>
</head>
<body>
<main class="canvas">

  <section class="card card--front" aria-label="Business card front">
    <div class="brand">
      <span class="brand__square"></span>
      <span class="brand__name">Sparrow Haulage</span>
    </div>

    <div class="contact">
      <p class="contact__name">Martin Obuya</p>
      <p class="contact__role">CEO/FOUNDER</p>
      <ul class="contact__list">
        <li class="contact__item">
          <svg class="contact__icon" viewBox="0 0 24 24" aria-hidden="true">
            <path fill="var(--red)" d="M6.6 10.8a15.1 15.1 0 0 0 6.6 6.6l2.2-2.2c.3-.3.7-.4 1-.2 1.1.4 2.3.6 3.6.6.6 0 1 .4 1 1V20c0 .6-.4 1-1 1A17 17 0 0 1 3 4c0-.6.4-1 1-1h3.5c.6 0 1 .4 1 1 0 1.3.2 2.5.6 3.6.1.3 0 .7-.2 1z"/>
          </svg>
          555-206-7142
        </li>
        <li class="contact__item">
          <svg class="contact__icon" viewBox="0 0 24 24" aria-hidden="true">
            <rect x="2" y="5" width="20" height="14" rx="1.5" fill="var(--red)"/>
            <path d="M3 6.5l9 6.5 9-6.5" fill="none" stroke="#fff" stroke-width="1.6"/>
          </svg>
          martinobuya@sparrow-haulage.example
        </li>
      </ul>
    </div>

    <svg class="front-graphic" viewBox="0 0 250 256" role="img" aria-label="Large brand mark decoration in navy and red">
      <defs>
        <linearGradient id="frontTone" x1="0" y1="0" x2="1" y2="1">
          <stop offset="0" stop-color="#1c1a5c"/>
          <stop offset="1" stop-color="#b31f27"/>
        </linearGradient>
      </defs>
      <rect x="0" y="0" width="250" height="256" fill="url(#frontTone)"/>
    </svg>
  </section>

  <section class="card card--back" aria-label="Business card back">
    <svg class="back-pattern" viewBox="0 0 640 366" preserveAspectRatio="none" role="img" aria-label="Faint repeating brand pattern in light grey">
      <defs>
        <linearGradient id="backTone" x1="0" y1="0" x2="1" y2="1">
          <stop offset="0" stop-color="#e6e6e6"/>
          <stop offset="1" stop-color="#f8f8f8"/>
        </linearGradient>
      </defs>
      <rect width="640" height="366" fill="url(#backTone)"/>
    </svg>
    <span class="back-mark" role="img" aria-label="Brand symbol"></span>
  </section>

</main>
</body>
</html>
```